Wordpress Design for a Digital Management Consulting Business

I need a simple Wordpress Design and someone to set it up for a new boutique management consulting business called Quillon Advisory that specialises in providing strategic advice to help grow digital businesses. It covers business strategy, marketing strategy, digital strategy, web product development, marketing campaigns, social, search, etc. From strategy to implementation.

URL is: quillonadvisory.com.au

My professional background is here: au.linkedin.com/in/hollyprenwick

Competitors: other boutique digital/marketing management consulting businesses in Australia

The logos, colours and fonts are attached.

I would like the site to convey a business that is Smart/intelligent, Contemporary, Progressive, Digital, Energetic, Friendly.

The objective of the site is to educate visitors about what Quillon Advisory does and encourage them to contact me for more information. It will be very light on content.

Target Market(s)

CEOs/Managing Directors, General Managers, Marketing Directors

Industry/Entity Type

Management Consulting

Font styles to use
Sans Serif

Colors
e34197
5c5c5c
000000

Requirements
Must have
• Site design requirements:
• Choose an appropriate Wordpress template, set it up for me and let me be able to edit it ongoing.
• It should use lots of images - these can be inspirational and not necessarily tied directly to the work
• Pink should feature, but not be the dominant colour.
• Site structure should be:
• 1. Home page - image led with horizontal navigation. Text beneath and images to describe the services.
• 2. About page - with space to write text and insert a picture of the Director
• 3. Services - with space to highlight services either as a list or graphically with text
• 4. Contact page - with space to write text and add email links, etc.
• Should have horizontal navigation
• It should have the flexibility to add another page
Nice to have
• Use the tree icon somehow in the design - consider in the background enlarged
• Use pink, grey, black from logo. Can introduce another complimentary colour if necessary.
• Can introduce another complimentary font to go with the logo font.
Should not have
• Use cliched business images and icons, eg. business suits, hand shakes, business men, business ties.

```html
<!DOCTYPE html>
<html lang="en">
<head>
<meta charset="utf-8">
<title>Quillon Advisory – Professional Consulting Services</title>
<link href="https://fonts.googleapis.com/css2?family=Open+Sans:wght@400;600;700;800&family=Montserrat:wght@500;600;700&display=swap" rel="stylesheet">
<style>
  :root{
    --pink:#e34197;
    --pink-dark:#c9337f;
    --grey:#5c5c5c;
    --grey-light:#ececec;
    --grey-line:#d4d4d4;
    --black:#000000;
    --ink:#2b2b2b;
    --footer:#2e2e2e;
    --white:#ffffff;
  }
  *{box-sizing:border-box;margin:0;padding:0}
  html,body{width:1200px;height:2400px;overflow:hidden}
  body{font-family:"Open Sans",Arial,sans-serif;color:var(--grey);background:var(--white)}
  .wrap{width:1000px;margin:0 auto;position:relative}

  /* header */
  .site-header{height:80px;background:var(--white)}
  .site-header .wrap{height:80px;display:flex;align-items:center;justify-content:space-between}
  .brand{display:flex;align-items:center;gap:12px}
  .brand-dot{width:30px;height:30px;border-radius:50%;background:var(--pink)}
  .brand-name{font-family:"Montserrat",sans-serif;font-weight:600;font-size:30px;color:var(--pink);letter-spacing:1px;text-transform:uppercase}
  .social{display:flex;gap:12px}
  .social span{width:16px;height:16px;border-radius:50%;background:var(--grey)}

  .main-nav{height:38px;background:var(--pink)}
  .main-nav ul{list-style:none;display:flex;height:38px;align-items:center}
  .main-nav li{font-family:"Montserrat",sans-serif;font-size:13px;font-weight:600;color:var(--white);padding:0 18px;height:38px;line-height:38px;text-transform:uppercase}
  .main-nav li.active{background:var(--black)}

  /* hero */
  .hero{position:relative;height:584px;overflow:hidden}
  .hero-photo{position:absolute;inset:0;background:linear-gradient(160deg,#8d939c 0%,#5a606a 35%,#3a3e46 70%,#60656e 100%)}
  .hero-shade{position:absolute;inset:0;background:rgba(20,22,28,.45)}
  .hero-copy{position:relative;text-align:center;color:var(--white);padding-top:150px}
  .hero-title{font-size:84px;font-weight:700;letter-spacing:4px;line-height:1}
  .hero-sub{font-size:34px;font-weight:400;letter-spacing:3px;margin-top:20px}
  .hero-tag{font-size:20px;letter-spacing:1.5px;margin-top:22px;text-transform:uppercase}
  .btn-outline{display:inline-block;margin-top:60px;border:2px solid var(--white);padding:12px 26px;font-size:16px;letter-spacing:1px;color:var(--white)}
  .hero-rule{position:absolute;left:0;right:0;bottom:0;height:10px;background:var(--pink)}

  /* welcome */
  .welcome{height:262px;text-align:center;padding-top:32px}
  .welcome-mark{width:34px;height:34px;border-radius:50%;background:var(--pink);margin:0 auto}
  .section-title{font-family:"Montserrat",sans-serif;font-weight:700;font-size:30px;color:var(--ink);letter-spacing:1px;text-transform:uppercase}
  .welcome .section-title{margin-top:18px}
  .welcome p{width:900px;margin:18px auto 0;font-size:14px;line-height:22px}

  /* services */
  .services{height:578px;background:var(--grey-light);padding-top:70px}
  .heading-ruled{display:flex;align-items:center;justify-content:center;gap:24px}
  .heading-ruled::before,.heading-ruled::after{content:"";width:330px;height:1px;background:var(--grey-line)}
  .cards{display:flex;justify-content:space-between;margin-top:50px}
  .card{width:300px;background:var(--white);height:390px}
  .card-photo{height:150px}
  .card-photo.digital{background:linear-gradient(135deg,#2c3440,#6c7684,#c5ccd5)}
  .card-photo.marketing{background:linear-gradient(135deg,#e8eef4,#a9c3dc,#f1d2a3)}
  .card-photo.transform{background:linear-gradient(135deg,#1d3b66,#4e7fb8,#b9d3ee)}
  .card-body{padding:20px 16px}
  .card h3{font-size:21px;font-weight:600;color:var(--ink)}
  .card p{font-size:12.5px;line-height:19px;margin-top:12px}
  .read-more{display:block;margin-top:14px;font-size:12px;font-weight:700;color:var(--ink)}

  /* what we do */
  .what{height:546px;padding-top:56px}
  .features{display:flex;justify-content:space-between;margin-top:50px}
  .feature{width:300px;text-align:center}
  .feature svg{display:block;margin:0 auto}
  .feature h3{font-size:20px;font-weight:700;color:var(--ink);margin-top:18px}
  .feature p{font-size:13px;line-height:20px;margin-top:12px;padding:0 10px}

  /* footer */
  .site-footer{height:262px;background:var(--footer);color:#cfcfcf;padding-top:34px}
  .footer-cols{display:flex}
  .footer-col h4{font-size:18px;font-weight:700;line-height:24px;color:var(--white);margin-bottom:14px}
  .footer-col ul{list-style:none}
  .footer-col li{font-size:12.5px;line-height:22px;padding-left:16px;position:relative}
  .footer-col li::before{content:"";position:absolute;left:0;top:8px;width:6px;height:6px;border-radius:50%;background:#cfcfcf}
  .col-nav{width:200px}
  .col-services{width:440px;display:flex;gap:40px}
  .col-services .list-block{width:200px}
  .col-services .list-block.continued{padding-top:38px}
  .col-contact{width:360px}
  .col-contact p{font-size:12.5px;line-height:20px}
  .col-contact strong{color:var(--white)}
  .footer-bar{height:56px;background:var(--pink);color:var(--white);font-size:12px;text-align:center;line-height:56px}
</style>
</head>
<body>

<header class="site-header">
  <div class="wrap">
    <div class="brand"><span class="brand-dot"></span><span class="brand-name">Quillon Advisory</span></div>
    <div class="social" aria-label="Social links"><span></span><span></span><span></span><span></span><span></span></div>
  </div>
</header>

<nav class="main-nav">
  <div class="wrap">
    <ul>
      <li class="active">Home</li><li>About Us</li><li>Services</li><li>Products</li><li>News</li><li>Contact Us</li>
    </ul>
  </div>
</nav>

<section class="hero">
  <div class="hero-photo" role="img" aria-label="Photo of a desk with laptop and business charts"></div>
  <div class="hero-shade"></div>
  <div class="hero-copy">
    <h1 class="hero-title">PROFESSIONAL</h1>
    <div class="hero-sub">CONSULTING SERVICES</div>
    <div class="hero-tag">We are the trusted advisor to the world's leading businesses</div>
    <span class="btn-outline">LEARN MORE</span>
  </div>
  <div class="hero-rule"></div>
</section>

<section class="welcome">
  <div class="welcome-mark"></div>
  <h2 class="section-title">Welcome to Quillon Advisory</h2>
  <p>Quillon Advisory is a boutique management consulting company advising businesses in the digital, ecommerce, media, travel, technology and finance sectors on business, product and marketing strategy. Combining strategic thinking with digital knowhow and marketing expertise, Quillon Advisory works with businesses looking to accelerate growth, diversify or increase profit of a new or existing digital business.</p>
</section>

<section class="services">
  <div class="wrap">
    <h2 class="section-title heading-ruled">Our Services</h2>
    <div class="cards">
      <article class="card">
        <div class="card-photo digital" role="img" aria-label="Photo of a person working with digital devices"></div>
        <div class="card-body">
          <h3>Digital Strategy</h3>
          <p>With over 15 years experience in digital businesses, Quillon Advisory develops business, product, sales &amp; marketing strategies with a focus on accelerating or establishing digital businesses.</p>
          <span class="read-more">READ MORE</span>
        </div>
      </article>
      <article class="card">
        <div class="card-photo marketing" role="img" aria-label="Photo of marketing plans and notes on a desk"></div>
        <div class="card-body">
          <h3>Marketing Consultation</h3>
          <p>Whether you have a new product or want to accelerate growth of an existing business, Quillon Advisory can define a robust marketing strategy and implement a successful marketing campaign.</p>
          <span class="read-more">READ MORE</span>
        </div>
      </article>
      <article class="card">
        <div class="card-photo transform" role="img" aria-label="Photo of a touchscreen with network graphics"></div>
        <div class="card-body">
          <h3>Digital Transformation</h3>
          <p>Quillon Advisory works with businesses to create a digital competitive advantage, identifying new opportunities and building digital capabilities.</p>
          <span class="read-more">READ MORE</span>
        </div>
      </article>
    </div>
  </div>
</section>

<section class="what">
  <div class="wrap">
    <h2 class="section-title heading-ruled">What We Do</h2>
    <div class="features">
      <div class="feature">
        <svg width="150" height="170" viewBox="0 0 150 170">
          <polygon points="75,4 144,44 144,126 75,166 6,126 6,44" fill="var(--pink)"/>
          <circle cx="75" cy="74" r="24" fill="none" stroke="#fff" stroke-width="5"/>
          <rect x="63" y="100" width="24" height="8" fill="#fff"/>
          <rect x="66" y="112" width="18" height="6" fill="#fff"/>
        </svg>
        <h3>Strategic thinking</h3>
        <p>Working with CEO, MDs and functional leaders, Quillon Advisory evaluates business problems and identifies new opportunities for growth.</p>
      </div>
      <div class="feature">
        <svg width="150" height="170" viewBox="0 0 150 170">
          <polygon points="75,4 144,44 144,126 75,166 6,126 6,44" fill="var(--white)" stroke="var(--grey-line)" stroke-width="3"/>
          <polyline points="42,110 64,80 84,96 110,60" fill="none" stroke="var(--grey)" stroke-width="7" stroke-linecap="round" stroke-linejoin="round"/>
          <polygon points="98,58 114,54 110,70" fill="var(--grey)"/>
        </svg>
        <h3>Analytical approach</h3>
        <p>Recommendations are based on robust research with key stakeholders, in-depth analysis, industry, competitor and customer insight, and a depth of digital and marketing knowledge.</p>
      </div>
      <div class="feature">
        <svg width="150" height="170" viewBox="0 0 150 170">
          <polygon points="75,4 144,44 144,126 75,166 6,126 6,44" fill="var(--white)" stroke="var(--grey-line)" stroke-width="3"/>
          <circle cx="75" cy="85" r="28" fill="none" stroke="var(--grey)" stroke-width="10" stroke-dasharray="11 6"/>
          <circle cx="75" cy="85" r="11" fill="var(--grey)"/>
        </svg>
        <h3>Implementation</h3>
        <p>Quillon Advisory will develop a road map to implement the strategy, connect the changes within your organisation or act as end-to-end project.</p>
      </div>
    </div>
  </div>
</section>

<footer>
  <div class="site-footer">
    <div class="wrap footer-cols">
      <div class="footer-col col-nav">
        <h4>Navigation</h4>
        <ul><li>Home</li><li>About Us</li><li>Services</li><li>Projects</li><li>News</li><li>Contact Us</li></ul>
      </div>
      <div class="footer-col col-services">
        <div class="list-block">
          <h4>Our Services</h4>
          <ul><li>Digital Strategy</li><li>Business Strategy</li><li>Product and Content Strategy</li><li>Growth Strategy</li><li>Sales and Marketing Strategy</li></ul>
        </div>
        <div class="list-block continued">
          <ul><li>Digital Strategy</li><li>Business Strategy</li><li>Product and Content Strategy</li><li>Growth Strategy</li><li>Sales and Marketing Strategy</li></ul>
        </div>
      </div>
      <div class="footer-col col-contact">
        <h4>Get in Touch</h4>
        <p><strong>For more information about what we do, please contact:</strong></p>
        <p>Wren Talmadge (Director)<br>Quillon Advisory<br>M: 0400 557 204<br>E: info@quillonadvisory.com.au</p>
      </div>
    </div>
  </div>
  <div class="footer-bar">Quillon Advisory © 2015 Privacy policy</div>
</footer>

</body>
</html>
```